Visitenkarten für Planung und Installation von Photovoltaikanlagen auf Wohnhäusern
Zielgruppe
Planung und Installation von Photovoltaikanlagen auf Wohnhäusern.
Komplettlösungen inkl. Energiespeicher (Batterien) und Wallboxen für Elektrofahrzeuge.
Logo
Solvimeta
Merten Holzfeld (Inhaber)
Festnetz 017648293051
Mobil 017648293051
merten@solvimeta.de
solvimeta.de
Im Wiesengrund 7
58213 Kattenvenne
QR-Code für V-Card

```html
<!DOCTYPE html>
<html lang="de">
<head>
<meta charset="utf-8">
<title>Solvimeta – Visitenkarte</title>
<link rel="stylesheet" href="https://fonts.googleapis.com/css2?family=Montserrat:wght@500;600;800&family=Arimo:wght@400&display=swap">
<style>
  :root {
    --green: #619a42;
    --grey: #727272;
    --text-grey: #6b6b6b;
    --white: #ffffff;
    --page: #ffffff;
  }
  * { margin: 0; padding: 0; box-sizing: border-box; }
  html, body {
    width: 849px; height: 1200px; overflow: hidden;
    background: var(--page);
  }
  .card {
    position: absolute;
    left: 111px;
    width: 639px;
    height: 344px;
    overflow: hidden;
  }
  .card--front { top: 237px; background: var(--green); }
  .card--back { top: 637px; background: var(--white); outline: 1px solid #e4e4e4; }

  .brand {
    position: absolute;
    font-family: "Montserrat", sans-serif;
    text-align: center;
  }
  .brand__name {
    font-weight: 800;
    letter-spacing: 1px;
    line-height: 1;
  }
  .brand__tagline {
    font-weight: 600;
    letter-spacing: 3.4px;
    line-height: 1;
  }
  .card--front .brand {
    left: 0; right: 0; top: 138px;
    color: var(--white);
  }
  .card--front .brand__name { font-size: 34px; }
  .card--front .brand__tagline { font-size: 15px; margin-top: 10px; }

  .card--back .brand {
    left: 28px; width: 262px; top: 168px;
  }
  .card--back .brand__name { font-size: 26px; color: var(--green); }
  .card--back .brand__tagline { font-size: 12px; margin-top: 8px; color: var(--text-grey); letter-spacing: 2.6px; }

  .divider {
    position: absolute;
    left: 347px; top: 55px;
    width: 3px; height: 234px;
    background: var(--grey);
  }

  .person {
    position: absolute;
    left: 408px; top: 62px;
    width: 202px;
    text-align: center;
    font-family: "Montserrat", sans-serif;
  }
  .person__name {
    font-size: 20px; font-weight: 600;
    color: var(--text-grey);
    letter-spacing: 0.5px;
    white-space: nowrap;
  }
  .person__role {
    font-size: 13px; font-weight: 600;
    color: var(--green);
    letter-spacing: 1.6px;
    margin-top: 3px;
  }

  .contacts {
    position: absolute;
    left: 408px; top: 122px;
    list-style: none;
    font-family: "Arimo", sans-serif;
    font-size: 15.5px;
    color: var(--text-grey);
  }
  .contacts__item {
    display: flex; align-items: center;
    height: 26px;
    margin-bottom: 17px;
  }
  .contacts__item:nth-child(3) { margin-bottom: 20px; }
  .contacts__icon { width: 26px; height: 26px; flex: none; margin-right: 15px; }

  .band { position: absolute; bottom: 0; }
  .band--grey { left: 340px; right: 0; height: 10px; background: var(--grey); }
  .band--green { left: 0; width: 350px; height: 19px; }
</style>
</head>
<body>

<section class="card card--front">
  <div class="brand">
    <div class="brand__name">SOLVIMETA</div>
    <div class="brand__tagline">DIE PHOTOVOLTAIK PROFIS</div>
  </div>
</section>

<section class="card card--back">
  <div class="brand">
    <div class="brand__name">SOLVIMETA</div>
    <div class="brand__tagline">DIE PHOTOVOLTAIK PROFIS</div>
  </div>

  <div class="divider"></div>

  <div class="person">
    <div class="person__name">MERTEN HOLZFELD</div>
    <div class="person__role">Inhaber</div>
  </div>

  <ul class="contacts">
    <li class="contacts__item">
      <svg class="contacts__icon" viewBox="0 0 26 26" aria-hidden="true">
        <circle cx="13" cy="13" r="13" fill="var(--green)"/>
        <path d="M8 15.5c1.5 2 3 3.2 4.8 3.8l1.6-1.6-2-1.6-1 .8c-.8-.5-1.5-1.2-2-2l.8-1-1.6-2L7 13.5c.2.7.5 1.4 1 2z" fill="#fff"/>
        <path d="M14 8.2a4 4 0 0 1 3.8 3.8M14 10.4a1.8 1.8 0 0 1 1.6 1.6" stroke="#fff" stroke-width="1.2" fill="none"/>
      </svg>
      <span>017648293051</span>
    </li>
    <li class="contacts__item">
      <svg class="contacts__icon" viewBox="0 0 26 26" aria-hidden="true">
        <circle cx="13" cy="13" r="13" fill="var(--green)"/>
        <rect x="9.5" y="6.5" width="7" height="13" rx="1" fill="none" stroke="#fff" stroke-width="1.4"/>
      </svg>
      <span>017648293051</span>
    </li>
    <li class="contacts__item">
      <svg class="contacts__icon" viewBox="0 0 26 26" aria-hidden="true">
        <circle cx="13" cy="13" r="13" fill="var(--green)"/>
        <rect x="6.5" y="8.5" width="13" height="9" fill="#fff"/>
        <path d="M6.5 8.5l6.5 5 6.5-5" fill="none" stroke="var(--green)" stroke-width="1"/>
      </svg>
      <span>merten@solvimeta.de</span>
    </li>
    <li class="contacts__item">
      <svg class="contacts__icon" viewBox="0 0 26 26" aria-hidden="true">
        <g fill="none" stroke="var(--green)" stroke-width="1.8">
          <circle cx="13" cy="13" r="11.5"/>
          <ellipse cx="13" cy="13" rx="5" ry="11.5"/>
          <line x1="13" y1="1.5" x2="13" y2="24.5"/>
          <line x1="1.5" y1="13" x2="24.5" y2="13"/>
          <line x1="3.5" y1="7.5" x2="22.5" y2="7.5"/>
          <line x1="3.5" y1="18.5" x2="22.5" y2="18.5"/>
        </g>
      </svg>
      <span>solvimeta.de</span>
    </li>
  </ul>

  <div class="band band--grey"></div>
  <svg class="band band--green" viewBox="0 0 350 19" preserveAspectRatio="none" aria-hidden="true">
    <polygon points="0,0 338,0 350,19 0,19" fill="var(--green)"/>
  </svg>
</section>

</body>
</html>
```